Broschüren-Design für Bauunternehmen
Zielgruppe
Wir bauen Neubauten in Massiv Bauweise, als Bauträger und Generalunternehmer in Raum Baden-Baden und Umgebung. Zielgruppe sind alle Altersgruppen, jedoch möchten wir gerade junge Familien mit Kindern unterstützen ihr e induvidueles Traumhaus mit Festpreis Garantien kostenbewusst zu ermöglichen.
Aufgabenstellung
Es sollte eine Image Broschüre Größe A4 in 12 Seiten ergeben. Unter Berücksichtigung dass es ein Imagespiegelung unseres website
design sollte.
Die Textinhalte sollten aus der Webseite übernommen werden und dürfen auch passend gekürzt werden.
Logo, Bilder welches in der Webseite ersichtlich sind sollten verwendet werden. Es können jedoch stock-bilder, Vektor Dateien bei bedarf verwendet werden. Diese werden dann dazu gekauft.
Inhalt:
Seite 1 - Startbild, Logo und Überschrift „Fest-gefügt - Rundum aus einem Guss - Vorlind Bauunternehmung aus Baden-Baden!'
Seite 2 - Philosophie, Bild Geschäftsführer; (Text siehe Startseite unter „Wir sind als Bauträger..........Wir beraten Sie gerne!')
Seite 3 - Über Uns, Bild Beratung (Text siehe über uns)
Seite 4 / 5 - Rundum Sicherheitspaket, Bilder Hand und Familie und Garantie Siegel (Text Leistungen/Sicherheitspaket)
Seite 6/7 - Bauberatung Bilder siehe Webseite
Seite 8 - Massivbau und Monolithische Bauweise ( Text Bauwissen/Massivbau und Bauwissen/Monolithische Bauweise) Wichtig Text passend kürzen.....
Seite 9 - Wohnraumlüftung - Bild siehe Webseite (Text Bauwissen/Raumklima)
Seite 10/11 - Finanzierung und BRT-Standards (Text Bauwissen)
Seite 12 - Kontakt und Adresse
Wie gesagt Designfarbe wie Webseite und logo. Längere Texte können zweispaltig geschrieben werden. Texte können gekürzt werden.
Bild Herkünfte siehe Impressum. können bei stock als Entwurf heruntergeladen werden. bei Finnisch werden sie nachgereicht.

```html
<!DOCTYPE html>
<html lang="de">
<head>
<meta charset="utf-8">
<title>Vorlind Bauunternehmung – Broschüre</title>
<link rel="stylesheet" href="https://fonts.googleapis.com/css2?family=Open+Sans:wght@300;400;600;700&display=swap">
<style>
:root{
  --stage:#3f423d;
  --paper:#ffffff;
  --paper-grey:#ededec;
  --gold:#e6ae1f;
  --ink:#3c3c3c;
  --ink-soft:#6a6a6a;
  --tick:#6fb43f;
  --shade:#e4e4e2;
  --seal-green:#6f8a5a;
}
*{box-sizing:border-box;margin:0;padding:0}
html,body{width:1200px;height:2400px;overflow:hidden}
body{background:var(--stage);font-family:"Open Sans",Arial,sans-serif;color:var(--ink);position:relative}
.spread{position:absolute;left:80px;width:1040px;height:735px;background:var(--paper);overflow:hidden}
.spread--about{top:49px}
.spread--safety{top:833px;background:var(--paper-grey)}
.spread--advice{top:1617px}
.abs{position:absolute}

/* about */
.quote-panel{left:24px;top:24px;width:471px;height:685px;background:var(--gold);
  clip-path:polygon(0 0,100% 0,100% 78%,62% 100%,0 100%)}
.quote-mark{left:20px;top:60px;font-size:150px;font-weight:700;color:#fff;line-height:1;letter-spacing:-14px}
.quote-text{left:134px;top:110px;width:345px;font-size:22px;font-weight:300;line-height:1.2;color:#fff}
.portrait{left:134px;top:386px;width:82px;height:174px;background:linear-gradient(180deg,#dcdcdc 0%,#a7a29b 45%,#2d2f35 100%)}
.ceo-text{left:276px;top:384px;width:180px;font-size:9.4px;line-height:1.7;color:#fff}
.ceo-text strong{display:block;margin-top:12px;font-weight:700}
.signature{left:134px;top:578px;width:90px;height:30px;background:linear-gradient(90deg,rgba(255,255,255,.45),rgba(255,255,255,.15))}
.ceo-name{left:134px;top:614px;font-size:9.5px;color:#fff}
.about-photo{left:578px;top:24px;width:462px;height:230px;background:linear-gradient(135deg,#e9e4da 0%,#cdbfa6 50%,#7a7e86 100%);
  clip-path:polygon(0 0,100% 0,100% 100%,38% 100%)}
.about-deco{left:520px;top:300px;width:520px;height:435px;background:var(--shade);opacity:.6;
  clip-path:polygon(55% 0,100% 40%,100% 100%,0 100%,0 55%)}
.section-title{font-size:20px;font-weight:400;color:var(--gold);line-height:1.2}
.about-title{left:593px;top:312px}
.about-lead{left:593px;top:350px;width:390px;font-size:10px;line-height:1.45}
.cols{left:593px;top:420px;width:390px;display:flex;gap:22px;font-size:7.6px;line-height:1.42;color:var(--ink)}
.cols p{margin-bottom:7px}
.cols div{flex:1}
.folio{right:24px;bottom:22px;font-size:8px;color:var(--ink-soft)}
.folio b{color:var(--gold);font-weight:400}

/* safety */
.safety-light{left:24px;top:24px;width:496px;height:685px;background:var(--paper)}
.hand-photo{left:24px;top:27px;width:496px;height:245px;background:linear-gradient(135deg,#f2efe9 0%,#d9c8b4 40%,#9c4f3a 60%,#6e8e45 100%);
  clip-path:polygon(10% 0,100% 0,100% 100%,0 100%,0 18%)}
.seal{left:330px;top:358px;width:146px;height:146px;border-radius:50%;background:#fff;border:10px solid var(--seal-green)}
.safety-title{left:68px;top:470px;width:260px}
.safety-copy{left:68px;top:540px;width:420px;font-size:9.4px;line-height:1.5}
.safety-copy p{margin-bottom:10px}
.safety-grid{left:572px;top:52px;width:440px;display:grid;grid-template-columns:1fr 1fr;column-gap:22px;row-gap:12px}
.benefit{position:relative;padding-left:18px;font-size:7.2px;line-height:1.38;min-height:95px}
.benefit h3{font-size:7.6px;font-weight:700;margin-bottom:2px;line-height:1.25}
.benefit svg{position:absolute;left:0;top:0;width:13px;height:11px}

/* advice */
.advice-gold-right{left:520px;top:24px;width:496px;height:685px;background:var(--gold)}
.advice-gold-left{left:24px;top:300px;width:496px;height:409px;background:var(--gold)}
.plans-photo{left:0;top:0;width:520px;height:402px;background:linear-gradient(150deg,#dadbd9 0%,#f1f1ef 45%,#bfbfbb 100%)}
.advice-title{left:68px;top:488px;width:420px;font-size:20px;font-weight:300;line-height:1.22;color:#fff}
.advice-copy{left:68px;top:560px;width:420px;font-size:8.8px;line-height:1.5;color:#fff}
.step{left:560px;width:440px;display:flex;gap:16px;color:#fff}
.step svg{flex:none;width:76px;height:76px}
.step h3{font-size:13px;font-weight:400;line-height:1.2;margin-bottom:8px}
.step p{font-size:7.2px;line-height:1.42;margin-bottom:6px}
.step-1{top:46px}.step-2{top:258px}.step-3{top:470px}
</style>
</head>
<body>

<section class="spread spread--about">
  <div class="abs quote-panel"></div>
  <div class="abs quote-mark">,,</div>
  <p class="abs quote-text">Wir sind als Bauträger und Generalunternehmer in Baden‑Baden Ihr kompetenter Ansprechpartner für die Region. Ihr Wunschhaus bauen wir schlüsselfertig oder mit Baueigenleistungen ganz nach Ihrem Geschmack.</p>
  <div class="abs portrait" role="img" aria-label="Porträtfoto des Geschäftsführers"></div>
  <p class="abs ceo-text">Der solide Bau hat an Beliebtheit nie verloren. Warum? Ganz einfach: Weil der solide Bau Stein auf Stein ein Haus hochwertig und haltbar zugleich macht. Wir stehen für die solide monolithische Ausführung unserer Projekte und verbinden modernes Bauen mit traditionsreichem Bauhandwerk. Ein schneller Baubeginn und Sorgfalt bei jeder Tätigkeit bringen Sie Ihrem Traumhaus im Massivbau Schritt für Schritt näher.<strong>Sprechen Sie uns an.<br>Wir beraten Sie gerne!</strong></p>
  <div class="abs signature" role="img" aria-label="Handschriftliche Unterschrift"></div>
  <p class="abs ceo-name">H. Vorlind</p>

  <div class="abs about-deco"></div>
  <div class="abs about-photo" role="img" aria-label="Foto: Beratungsgespräch mit einem jungen Paar"></div>
  <h2 class="abs section-title about-title">Über uns</h2>
  <p class="abs about-lead">Die Firma Vorlind Bauunternehmung als seriöser Anbieter von Dienstleistungen rund um den Hausbau steht für eine schnelle Umsetzung eines Bauprojekts, angefangen von der individuellen Planung bis hin zum abgeschlossenen Bau eines Hauses.</p>
  <div class="abs cols">
    <div>
      <p>Wir erfüllen Ihnen Ihren individuellen Traum vom Eigenheim und pflegen dazu Kontakte zu Partnern der entsprechenden Gewerke und auch zu Architekten, die Ihren individuellen Entwurf vom Traumhaus begleiten. Auch Baueigenleistungen Ihrerseits sind hierbei möglich.</p>
      <p>Unser oberstes Ziel ist es, Ihnen das Haus zu bauen oder bauen zu lassen, das zu Ihnen passt, ob es ein Massivbau Stein auf Stein, ein Einfamilienhaus als Doppel- oder Reihenhaus oder auch ein Energiesparhaus, gebaut nach den aktuellen Standards der Energieeffizienz BRT, ist, wir finden in einem persönlichen Gespräch das Richtige für Sie!</p>
      <p>Wir verfolgen die Philosophie der grundsoliden Qualität und legen dennoch besonderen</p>
    </div>
    <div>
      <p>Wert auf eine schnelle Umsetzung. Zur Firmenphilosophie gehören ebenfalls eine geradlinige Vorgehensweise, die Garantie für einen fairen Festpreis und die Umsetzung neuester im Baugewerbe gültigen Standards.</p>
      <p>Die Firma Vorlind Bauunternehmung versteht sich als Ihr regionaler Ansprechpartner in Sachen schnelle Umsetzung eines Bauprojekts, legt Wert auf individuelle Beratung sowie absolute Zuverlässigkeit und Seriosität in Baden-Baden und angrenzender Umgebung.</p>
      <p>Unser Büro befindet sich im Lindenweg 7 in Baden-Baden und ist somit zentral gelegen (in der Fußgängerzone) und sehr gut zu erreichen. Sie sind uns sehr willkommen mit Ihrer Anfrage auf ein individuelles Bauprojekt, wir kümmern uns um die schnelle Umsetzung!</p>
    </div>
  </div>
  <p class="abs folio">Über uns <b>/</b> 3</p>
</section>

<section class="spread spread--safety">
  <div class="abs safety-light"></div>
  <div class="abs hand-photo" role="img" aria-label="Foto: Hände, die ein kleines Haus schützend umfassen"></div>
  <div class="abs seal" role="img" aria-label="Garantiesiegel"></div>
  <h2 class="abs section-title safety-title">Planung und finanzielle Absicherung</h2>
  <div class="abs safety-copy">
    <p>Die Vorlind Bauunternehmung legt größten Wert auf die Sicherheit der Bauausführung sowie deren Qualität, eine zuverlässige Planung und die finanzielle Absicherung unserer Kunden.</p>
    <p>Ein wichtiger Teilbereich ist die Planung und finanzielle Absicherung Ihres Bauvorhabens. Diese stellen wir durch folgende Leistungen und Maßnahmen sicher.</p>
  </div>
  <div class="abs safety-grid">
    <div class="benefit"><svg viewBox="0 0 13 11"><path d="M1 6l4 4 7-9" fill="none" stroke="var(--tick)" stroke-width="2.4"/></svg>
      <h3>Mit Festpreisgarantie bauen</h3>Als Bauherr benötigen Sie finanzielle Sicherheit beim Bau Ihres Eigenheims. Wir garantieren Ihnen den mit Vertragsabschluss vereinbarten Preis für die nächsten zwölf Monate. Unsere Garantie gibt Ihnen die für jeden Eigenheimbesitzer unverzichtbare finanzielle Sicherheit.</div>
    <div class="benefit"><svg viewBox="0 0 13 11"><path d="M1 6l4 4 7-9" fill="none" stroke="var(--tick)" stroke-width="2.4"/></svg>
      <h3>Garantie der Vorlind Bauunternehmung für Bau und Sicherheiten</h3>Kunden von uns haben das Recht auf die maximale und solide Qualität aller Leistungen. Unsere Priorität liegt auf der Termintreue und der qualitativ hochwertigen Durchführung aller erbrachten Arbeiten.</div>
    <div class="benefit"><svg viewBox="0 0 13 11"><path d="M1 6l4 4 7-9" fill="none" stroke="var(--tick)" stroke-width="2.4"/></svg>
      <h3>Baufertigstellungs-Bürgschaft</h3>Unsere Baufertigstellungs-Bürgschaft gibt Ihnen Ihre zuverlässige Sicherheit. Auf Wunsch sichern wir alle Bauleistungen bis zur vereinbarten Höhe über eine Bürgschaft ab. Damit schützen wir Sie in jeder Situation vor bösen Überraschungen.</div>
    <div class="benefit"><svg viewBox="0 0 13 11"><path d="M1 6l4 4 7-9" fill="none" stroke="var(--tick)" stroke-width="2.4"/></svg>
      <h3>Zertifizierte Architekten kontrollieren als Bauleitung</h3>Die Bauleitung liegt ausschließlich in der Hand zertifizierter Architekten. Diese kontrollieren alle Baufortschritte sowie am Massivbau und arbeiten intensiv mit Bausachverständigen und Handwerkern zusammen.</div>
    <div class="benefit"><svg viewBox="0 0 13 11"><path d="M1 6l4 4 7-9" fill="none" stroke="var(--tick)" stroke-width="2.4"/></svg>
      <h3>Baugrundgutachten durch geol. Institut</h3>Noch vor Baubeginn benötigen Sie alle relevanten Informationen über die Bodenbeschaffenheit Ihres Grundstücks. Denn auf Basis dieser Werte erfolgt die statische Berechnung für Ihr zukünftiges Zuhause. Diese Daten sind ein Teil der Garantie für die Sicherheit des Gebäudes. Wir arbeiten mit einem renommierten Institut zusammen.</div>
    <div class="benefit"><svg viewBox="0 0 13 11"><path d="M1 6l4 4 7-9" fill="none" stroke="var(--tick)" stroke-width="2.4"/></svg>
      <h3>Schriftliche Baudokumentation in Form eines Bau-Tagebuchs</h3>Jeder Arbeitsschritt wird schriftlich dokumentiert. Diese aufwendige Form eines Bau-Tagebuchs gewährleistet die gewissenhafte Ausführung aller Arbeiten und die Nachvollziehbarkeit der verwendeten Materialien sowie der entstandenen Kosten.</div>
    <div class="benefit"><svg viewBox="0 0 13 11"><path d="M1 6l4 4 7-9" fill="none" stroke="var(--tick)" stroke-width="2.4"/></svg>
      <h3>Unabhängiger Wirtschaftsprüfer verwaltet Baukonto</h3>Ihr Geld verwaltet ein unabhängiger Wirtschaftsprüfer. Alle durch Sie geleisteten Investitionen liegen auf einem eigenen Baukonto. Diese Maßnahme ist für Sie die Garantie, dass Ihr Geld ausschließlich für den von Ihnen bestimmten Zweck eingesetzt wird.</div>
    <div class="benefit"><svg viewBox="0 0 13 11"><path d="M1 6l4 4 7-9" fill="none" stroke="var(--tick)" stroke-width="2.4"/></svg>
      <h3>Unabhängige Sachverständige für das Qualitätsmanagement am Bau</h3>Wir arbeiten mit unabhängigen Sachverständigen zusammen. Diese kontrollieren in regelmäßigen Abständen die Qualität der einzelnen Baufortschritte sowie die solide Qualität der Ausführung.</div>
    <div class="benefit"><svg viewBox="0 0 13 11"><path d="M1 6l4 4 7-9" fill="none" stroke="var(--tick)" stroke-width="2.4"/></svg>
      <h3>Zahlungen nach §3 der Makler- und Bauträgerordnung</h3>Diese gesetzlich geregelte Form der Zahlungsvereinbarung gewährleistet die finanzielle Sicherheit der Kunden. Sie schützt Ihr Geld vor missbräuchlicher Verwendung und unberechtigtem Zugriff.</div>
    <div class="benefit"><svg viewBox="0 0 13 11"><path d="M1 6l4 4 7-9" fill="none" stroke="var(--tick)" stroke-width="2.4"/></svg>
      <h3>Blow-Door Test</h3>Wohngebäude mit kontrollierter Wohnraumlüftung erfordern den Blow-Door-Test. Dieser Test informiert über die Luft- und Winddichtheit des Massivbau-Gebäudes und ob Ihr neues Eigenheim die geforderten Werte erzielt.</div>
    <div class="benefit"><svg viewBox="0 0 13 11"><path d="M1 6l4 4 7-9" fill="none" stroke="var(--tick)" stroke-width="2.4"/></svg>
      <h3>Baubeginn und Bauzeitgarantie</h3>Bei uns erhalten Sie die Garantie für den vereinbarten Baubeginn sowie die Fertigstellung des Objekts. Sie planen mit dem zuverlässigen Zeitpunkt für den Umzug in Ihr neues Zuhause.</div>
    <div class="benefit"><svg viewBox="0 0 13 11"><path d="M1 6l4 4 7-9" fill="none" stroke="var(--tick)" stroke-width="2.4"/></svg>
      <h3>Energieausweis</h3>Die moderne Zeit bietet beim Massivbau zahlreiche Möglichkeiten der Energieeinsparung. Der Energieausweis nach der Energie-Einsparverordnung bestätigt die leistungsfähige Dämmung und den geringen Energieverbrauch Ihres Hauses.</div>
  </div>
</section>

<section class="spread spread--advice">
  <div class="abs advice-gold-right"></div>
  <div class="abs advice-gold-left"></div>
  <div class="abs plans-photo" role="img" aria-label="Foto: Hände über Bauplänen mit Taschenrechner und Brille"></div>
  <h2 class="abs advice-title">Professionelle Bauberatung:<br>Die Garantie für gehobene Qualität</h2>
  <p class="abs advice-copy">Für Ihren anstehenden Neubau ist eine fundierte und fachgerechte Bauberatung zu empfehlen. Mit uns als Experten erhalten Sie die Sicherheit, Ihr Objekt im Massivbau nach Ihren expliziten Wohnbedürfnissen umzusetzen und von einer exakten Anpassung an Ihr Baubudget zu profitieren. Die Vorlind Bauunternehmung bietet Ihnen eine fachkundige Bauberatung mit Garantie, die als Komplettangebot mit Garantie Ihre Bedürfnisse in den Vordergrund stellt und Qualität zum Festpreis bietet.</p>

  <div class="abs step step-1">
    <svg viewBox="0 0 76 76" fill="none" stroke="#fff" stroke-width="1.6"><circle cx="38" cy="38" r="36"/><path d="M22 52l26-26 4 4-26 26h-4z"/><path d="M24 22l30 30M28 26l3-3M33 31l3-3M38 36l3-3M43 41l3-3"/></svg>
    <div><h3>Die Planung<br>Ihres Bauprojekts mit uns als Fachbetrieb</h3>
      <p>Grundlage unserer fachkundigen Bauplanung ist der Abschluss eines Bauleistungsvertrags zu Festpreisen mit Garantie, für den Sie selbstverständlich ein 14-tägiges Rücktrittsrecht besitzen. Hiernach beginnt unser Architekt als Partner mit der individuellen Objektplanung und erstellt erste Entwürfe, ein Geologe erstellt ein Baugrundgutachten.</p>
      <p>Für ein zeitgemäßes Energiekonzept vertrauen wir auf einen Energieberater als Partner, der für Sie ein Wärmekonzept nach Ihren Wünschen entwickelt. In den folgenden Schritten übernehmen unsere Statiker und Architekten die Bauantragsplanung sowie die Erstellung von Werkplan und Statikplan. Die Erteilung der Baugenehmigung erfolgt im Regelfall binnen vier bis sechs Wochen.</p></div>
  </div>
  <div class="abs step step-2">
    <svg viewBox="0 0 76 76" fill="none" stroke="#fff" stroke-width="1.6"><circle cx="38" cy="38" r="36"/><rect x="22" y="24" width="32" height="28" rx="2"/><path d="M22 32h32M29 20v7M47 20v7"/><circle cx="31" cy="48" r="7"/><path d="M31 44v4h3"/></svg>
    <div><h3>Die Bauzeit –<br>schnelle Umsetzung für Ihre Zufriedenheit</h3>
      <p>Sobald die Baugenehmigung vorliegt, nehmen unsere Partner-Baufirmen innerhalb von zwei bis drei Monaten die Arbeit auf und sorgen für eine schnelle Umsetzung. Unsere Baupartner übernehmen während der gesamten Bauphase die verschiedenen Gewerke, die Leitung unterliegt unseren Partner-Architekten. Dieser sichert Ihnen zu, alle Aktivitäten rund um Ihren Neubau sachgerecht zu dokumentieren.</p>
      <p>Die Durchführung verschiedener Bauabschnitte wird durch Gutachter und Sachverständige (Prüfwerk, Baucert) während der Bauphase überprüft und entsprechend für Ihr Bauobjekt zertifiziert. Im Energiebereich führen unsere Berater einen Blow-Door-Test für eine optimale Wärmedämmung Ihres Gebäudes aus. Die Fertigstellung Ihres Baus sichern wir Ihnen abhängig von den Rahmenbedingungen binnen sechs Monaten nach Baubeginn zu.</p></div>
  </div>
  <div class="abs step step-3">
    <svg viewBox="0 0 76 76" fill="none" stroke="#fff" stroke-width="1.6"><circle cx="38" cy="38" r="36"/><circle cx="48" cy="28" r="8"/><circle cx="48" cy="28" r="2.5"/><path d="M42 34L22 54M26 50l4 4M30 46l3 3"/></svg>
    <div><h3>Die Bauübergabe –<br>der solide und seriöse Abschluss</h3>
      <p>Neben unseren Terminvereinbarungen für einzelne Ausbaustufen können Sie Ihren neuen Massivbau gerne auch schlüsselfertig nach kompletter Fertigstellung in Empfang nehmen. Bei Zwischenabnahmen und zum Ende hin werden Protokolle erstellt, mit denen sich jeder einzelne, in adäquater Qualität durchgeführte Schritt nachvollziehen lässt.</p>
      <p>Abschließend erhalten Sie von uns sämtliche Unterlagen wie Baupläne, Zertifikate, Materialnachweise und das Bautagebuch ausgehändigt. Auch den Energieausweis und natürlich Ihre Hausschlüssel nehmen Sie durch uns in Empfang und profitieren mit Garantie von einem einzigartigen Wohngefühl. Nutzen Sie den direkten Kontakt zu uns, um mehr über die Bauberatung der Vorlind Bauunternehmung zu erfahren und sich persönlich mit unseren Stärken vertraut zu machen.</p></div>
  </div>
</section>

</body>
</html>
```